Non fiction leadership Book Cover design needed for “Stay Bold: Build On Lasting Discipline”

I need a front cover design for a new book 6 X 9 traditional non-fiction book.

Title: "Stay BOLD - Build On Lasting Discipline"

The subtitle is not finalized- so use 2 lines of smaller dummy text

My brand guide is attached (please use the tan color sparingly)

I'd like to see BOLD look like it is in motion and "flying" across the page

Need CREATIVE designs and options

Do not want my picture on the front cover - I do want it on the back cover.

On the front cover I’d like to see creative use of font to create movement on “BOLD”

Target Market(s)

Business leaders

Industry/Entity Type

Aviation

Font styles to use
Other font styles liked:
• See style guide- can add additional font (modern script or san serif)

Colors
0054AA
0677BA
7BADD7
CADEEF
E8F1F8
EB3D1F
EC4F4E
F09395
F8D3D4
FCEDEE

Requirements
Must have
• Creative font use, using perspective to create movement/motion on BOLD
Should not have
• My picture on the front cover- my picture should be on the back cover

```html
<!DOCTYPE html>
<html lang="en">
<head>
<meta charset="utf-8">
<title>Stay BOLD - Build On Lasting Discipline</title>
<link href="https://fonts.googleapis.com/css2?family=Montserrat:wght@400;500;600;800&display=swap" rel="stylesheet">
<style>
  :root {
    --backdrop: #05071a;
    --paper: #f9f1ea;
    --title-red: #e1242e;
    --subtitle-grey: #4a4846;
    --body-ink: #1c1c1c;
    --author-tan: #8e4b16;
    --echo-grey: #6e6e6e;
  }
  html, body {
    margin: 0;
    padding: 0;
    width: 1200px;
    height: 1200px;
    overflow: hidden;
    background: var(--backdrop);
  }
  .canvas {
    position: relative;
    width: 1200px;
    height: 1200px;
    background: var(--backdrop);
    font-family: "Montserrat", sans-serif;
  }
  .cover {
    position: absolute;
    left: 230px;
    top: 44px;
    width: 740px;
    height: 1111px;
    background: var(--paper);
    overflow: hidden;
  }
  .motion-echo {
    position: absolute;
    transform-origin: center;
    white-space: nowrap;
    color: var(--echo-grey);
    font-weight: 600;
    letter-spacing: -0.02em;
    filter: blur(2.2px);
    opacity: 0.75;
    text-shadow: 6px 0 3px rgba(110,110,110,0.45), -6px 0 3px rgba(110,110,110,0.35);
  }
  .motion-echo b { font-weight: 800; }
  .title {
    position: absolute;
    left: 0;
    width: 100%;
    top: 388px;
    margin: 0;
    text-align: center;
    color: var(--title-red);
    font-size: 122px;
    line-height: 1;
    letter-spacing: -0.03em;
    white-space: nowrap;
  }
  .title-light { font-weight: 400; }
  .title-bold { font-weight: 800; }
  .subtitle {
    position: absolute;
    left: 0;
    width: 100%;
    top: 520px;
    margin: 0;
    text-align: center;
    color: var(--subtitle-grey);
    font-size: 42px;
    font-weight: 600;
    letter-spacing: -0.01em;
  }
  .blurb {
    position: absolute;
    left: 0;
    width: 100%;
    top: 862px;
    margin: 0;
    text-align: center;
    color: var(--body-ink);
    font-size: 15px;
    font-weight: 500;
    line-height: 1.22;
  }
  .author {
    position: absolute;
    left: 0;
    width: 100%;
    top: 1000px;
    margin: 0;
    text-align: center;
    color: var(--author-tan);
    font-size: 41px;
    font-weight: 600;
  }
</style>
</head>
<body>
<main class="canvas">
  <section class="cover" aria-label="Book cover">
    <div class="motion-echoes" aria-hidden="true">
      <span class="motion-echo" style="left:122px;top:111px;font-size:22px;transform:translate(-50%,-50%) skewX(-30deg)">Stay <b>BOLD</b></span>
      <span class="motion-echo" style="left:585px;top:102px;font-size:38px;transform:translate(-50%,-50%) skewX(-12deg) rotate(-3deg)">Stay <b>BOLD</b></span>
      <span class="motion-echo" style="left:363px;top:174px;font-size:24px;transform:translate(-50%,-50%) scaleY(0.8)">Stay <b>BOLD</b></span>
      <span class="motion-echo" style="left:140px;top:246px;font-size:30px;transform:translate(-50%,-50%) skewX(-28deg) rotate(-4deg)">Stay <b>BOLD</b></span>
      <span class="motion-echo" style="left:572px;top:240px;font-size:28px;transform:translate(-50%,-50%) skewX(-15deg)">Stay <b>BOLD</b></span>
      <span class="motion-echo" style="left:369px;top:281px;font-size:18px;transform:translate(-50%,-50%) scaleY(0.8)">Stay <b>BOLD</b></span>
      <span class="motion-echo" style="left:231px;top:631px;font-size:22px;transform:translate(-50%,-50%)">Stay <b>BOLD</b></span>
      <span class="motion-echo" style="left:589px;top:619px;font-size:21px;transform:translate(-50%,-50%) skewX(-22deg) rotate(-4deg)">Stay <b>BOLD</b></span>
      <span class="motion-echo" style="left:441px;top:654px;font-size:13px;transform:translate(-50%,-50%) skewX(-20deg)">Stay <b>BOLD</b></span>
      <span class="motion-echo" style="left:356px;top:740px;font-size:34px;transform:translate(-50%,-50%)">Stay <b>BOLD</b></span>
      <span class="motion-echo" style="left:130px;top:765px;font-size:22px;transform:translate(-50%,-50%) skewX(-18deg) rotate(4deg)">Stay <b>BOLD</b></span>
      <span class="motion-echo" style="left:585px;top:763px;font-size:22px;transform:translate(-50%,-50%) skewX(-30deg) rotate(-5deg)">Stay <b>BOLD</b></span>
    </div>
    <h1 class="title"><span class="title-light">Stay</span> <span class="title-bold">BOLD</span></h1>
    <p class="subtitle">Build On Lasting Discipline</p>
    <p class="blurb">Lorem ipsum dolor sit amet, consectetuer adipiscing elit,<br>sed diam nonummy nibh euismod tincidunt</p>
    <p class="author">Margaret Holloway</p>
  </section>
</main>
</body>
</html>
```